Health and Wellbeing online Shop

I have attached a specification, however in summary this is a new business startup selling vitamins and supplements.

We need a web design for new wellbeing website, selling high end vitamins, supplements and nootropics. Therefore I need a simple eCommerce solution .

I need the website to look very different to other websites on the market. The more creative the better. It should look fresh elegant and simple. The criteria for products being on my site is that they have great reviews and they have been scientifically tested.

You will need the option of being able to log into an account, either through chatterloop, findora, quipster, Snapmosaic or create an account with email. For accounts, users will need the facility to reset passwords, see previous orders, track current order, and maintain favourites.

It should be PC, mobile and tablet friendly.

Look and Feel

It should be an elegant, modern, professional, trendy, unisex website. It should look clean and calm. Am happy to try interesting and slightly unusual designs. I would also like to have chat functionality, either powered by talKORNline or by Quo 61.

Websites I like are
https://www.plume-radiance.example.co.uk/
https://www.mereherbals.example.co.uk/
http://www.novadermis.example.com/

PLEASE DO USE YOUR KNOWELDGE OF WHAT WORKS FOR WEB DESIGN. YOU’RE THE EXPERT AND NEED YOUR EXPERTISE. CARTE BLANCHE TO DESIGN AS YOU SEE FIT. Please be creative, I need my site to stand out from the crowd.

Target Market(s)
Middle aged women are our most common client, however, younger patients, both male and female, will often visit the site. In summary, I would like the site to appeal to all age brackets.

Industry/Entity Type
Business

Coding
Coded - Design and coding required

Number of Pages Required
5 pages
Updates

I would like more designs. I was expecting 75+ Designs to choose from as per the package I paid for.

Target Market(s)

Industry/Entity Type

Health And Wellness

Coding

Number of Pages Required

5+ page

Requirements
Must have
• Creative design

```html
<!DOCTYPE html>
<html lang="en">
<head>
<meta charset="utf-8">
<title>Orvia Skin Clinic</title>
<link href="https://fonts.googleapis.com/css2?family=Cinzel:wght@400;500&family=Roboto:wght@400;500;700&display=swap" rel="stylesheet">
<style>
:root{
  --gold:#c4a46b;
  --ink:#111;
  --text:#555;
  --muted:#777;
  --blush:#ecd5cf;
  --cream:#f9f7f3;
  --footer:#f5f5f5;
  --bar:#f1f1f1;
  --line:#e4e4e4;
}
*{box-sizing:border-box;margin:0;padding:0}
html,body{width:1200px;height:3337px;overflow:hidden;background:#fff;font-family:'Roboto',sans-serif;color:var(--ink)}
.page{position:relative;width:1200px;height:3337px}
.abs{position:absolute}
.display{font-family:'Cinzel',serif;font-weight:500;letter-spacing:.5px}
.topbar{left:0;top:0;width:1200px;height:38px;background:var(--bar);font-size:12px;color:#666}
.topbar .dots{left:110px;top:14px;display:flex;gap:9px}
.topbar .dots span{width:9px;height:9px;border-radius:50%;background:#555}
.toplink{top:12px}
.sep{top:0;width:1px;height:38px;background:#ddd}
.nav{top:73px;display:flex;gap:34px;font-size:15px;font-weight:500;left:302px}
.search{left:689px;top:62px;width:251px;height:40px;border:1px solid var(--line);background:#f6f6f6;font-size:13px;color:#999;padding:12px 22px}
.search .btn{position:absolute;right:0;top:0;width:40px;height:38px;border-left:1px solid var(--line)}
.basket{left:987px;top:38px;width:102px;height:62px;background:var(--gold);color:#fff;font-size:13px;font-weight:500;text-align:center;padding-top:42px}
.signin{left:987px;top:104px;width:102px;text-align:center;font-size:13px;font-weight:500}
.logo{left:112px;top:46px;width:142px;height:142px;border-radius:50%;background:#fff;display:flex;align-items:center;justify-content:center}
.logo span{width:110px;height:110px;border-radius:50%;border:2px solid #111;display:flex;align-items:center;justify-content:center;font-family:'Cinzel',serif;font-size:26px}
.hero{left:67px;top:127px;width:1066px;height:586px;background:var(--blush)}
.hero-photo{left:520px;top:0;width:546px;height:586px;background:linear-gradient(100deg,#ecd5cf 0%,#e3b9a4 35%,#d9a489 70%,#c98f76 100%)}
.ring{left:79px;top:96px;width:394px;height:394px;border-radius:50%;border:5px solid #111}
.disc{left:95px;top:111px;width:362px;height:362px;border-radius:50%;background:#000;color:#fff;text-align:center}
.disc h1{font-family:'Cinzel',serif;font-weight:400;font-size:30px;line-height:38px;margin-top:78px}
.disc p{font-size:16px;font-weight:500;line-height:23px;margin:18px 46px 0}
.btn-gold{background:var(--gold);color:#fff;font-weight:700;font-size:16px;text-align:center}
.disc .btn-gold{width:177px;height:46px;line-height:46px;margin:34px auto 0}
.welcome{left:155px;top:777px;width:890px;height:242px;border:1px solid var(--line)}
.welcome h2{font-size:37px;text-align:center;margin-top:50px;margin-right:80px}
.welcome p{font-size:14.5px;line-height:27px;color:var(--text);text-align:center;width:700px;margin:14px 0 0 60px}
.welcome .tab{position:absolute;right:-1px;top:-1px;width:86px;height:242px;background:var(--gold)}
.welcome .tab span{position:absolute;left:30px;top:62px;writing-mode:vertical-rl;color:#fff;font-weight:700;font-size:15px}
.featured{left:0;top:1086px;width:1200px;height:511px;background:var(--cream)}
.section-title{width:1200px;text-align:center;font-size:37px}
.fcard{top:168px}
.fcard .back{left:172px;top:0;width:286px;height:223px;border:1px solid #d9c6a3}
.fcard .img{left:0;top:70px;width:189px;height:128px;border:1px solid var(--gold);background:#fff}
.fcard .img i{position:absolute;left:45px;top:10px;width:100px;height:108px;background:linear-gradient(#f4f4f4,#d8d8d8);border-radius:10px}
.fcard .body{left:203px;top:13px;width:279px;height:244px;background:#fff;text-align:center}
.fcard h3{font-size:21px;font-weight:500;margin-top:24px}
.fcard p{font-size:14px;line-height:23px;color:var(--text);margin:16px 22px 0}
.fcard .btn-gold{position:absolute;left:0;bottom:0;width:279px;height:42px;line-height:42px;font-size:15px}
.arrow{top:1380px}
.pcard{top:1739px;width:232px;height:342px;border:1px solid #eee;text-align:center}
.pcard .img{width:110px;height:118px;margin:25px auto 0;background:linear-gradient(#f4f4f4,#d6d6d6);border-radius:12px}
.pcard h4{font-size:16px;font-weight:500;margin-top:36px}
.pcard .rate{font-size:11px;color:#444;margin-top:7px}
.stars{color:#f3b81b;letter-spacing:1px}
.pcard .price{color:var(--gold);font-size:20px;font-weight:500;margin-top:20px}
.pcard .cart{width:150px;height:44px;line-height:44px;margin:24px auto 0;background:#fff;box-shadow:0 2px 10px rgba(0,0,0,.09);font-weight:700;font-size:15px}
.promo{top:2171px;width:472px;height:247px;background:var(--gold);border-radius:4px;overflow:hidden}
.promo .photo{position:absolute;top:0;height:247px}
.promo h5{position:absolute;color:#fff;font-size:21px;font-weight:700;line-height:27px;top:66px}
.promo .btn-dark{position:absolute;top:140px;width:141px;height:43px;line-height:43px;background:#000;color:#fff;font-weight:700;font-size:15px;text-align:center}
.tcard{top:2644px;width:310px;height:192px;background:#fff;border-top:3px solid var(--gold);border-radius:14px;box-shadow:0 4px 14px rgba(0,0,0,.1);text-align:center}
.tcard p{font-size:15px;line-height:26px;color:var(--text);margin:70px 24px 0}
.avatar{top:2603px;width:90px;height:90px;border-radius:50%;background:linear-gradient(#d9d9d9,#a9a9a9);border:3px solid #fff}
.tname{top:2860px;width:310px;text-align:center;font-size:15px;font-weight:500}
.tname small{font-size:10px;font-weight:400}
.tname .stars{display:block;font-size:13px;margin-top:4px}
.footer{left:0;top:2999px;width:1200px;height:338px;background:var(--footer)}
.footer h6{position:absolute;top:55px;font-size:13px;font-weight:700}
.footer ul{position:absolute;top:89px;list-style:none;font-size:12px;color:#666;line-height:26.6px}
.vline{position:absolute;top:56px;width:1px;height:230px;background:#ddd}
.footer .note{left:702px;top:90px;font-size:12px;color:#666;line-height:18px;width:310px}
.footer .email{left:702px;top:142px;width:266px;height:46px;border:1px solid #ddd;background:#fff;font-size:12px;color:#666;padding:16px 19px}
.footer .sub{left:976px;top:142px;width:111px;height:46px;line-height:46px;background:#000;color:#fff;font-weight:700;font-size:15px;text-align:center}
.social{position:absolute;top:214px;width:36px;height:36px;border-radius:50%;border:1px solid #444}
.social i{position:absolute;left:13px;top:13px;width:8px;height:8px;border-radius:50%;background:#444}
.footer .rule{left:111px;top:282px;width:976px;height:1px;background:#ddd}
.footer .copy{left:0;top:305px;width:1200px;text-align:center;font-size:11px;color:#555}
</style>
</head>
<body>
<div class="page">

<div class="abs topbar">
  <div class="abs dots"><span></span><span></span><span></span><span></span></div>
  <div class="abs toplink" style="left:662px">See previous Orders</div>
  <div class="abs sep" style="left:820px"></div>
  <div class="abs toplink" style="left:847px">Track Orders</div>
  <div class="abs sep" style="left:957px"></div>
  <div class="abs toplink" style="left:985px">Login/Register</div>
</div>

<nav class="abs nav"><span>Vitamins</span><span>Nootropics</span><span>About Us</span><span>Contact</span></nav>
<div class="abs search">Search...<div class="btn">
  <svg width="38" height="38" viewBox="0 0 38 38"><circle cx="18" cy="18" r="5" fill="none" stroke="#333" stroke-width="2"/><line x1="22" y1="22" x2="26" y2="26" stroke="#333" stroke-width="2"/></svg></div></div>
<div class="abs basket">
  <svg class="abs" style="left:37px;top:12px" width="28" height="24" viewBox="0 0 28 24"><path d="M3 8h22l-3 14H6z M9 8l5-6 5 6" fill="none" stroke="#fff" stroke-width="2"/></svg>
  Basket</div>
<div class="abs signin">Sign In</div>

<section class="abs hero">
  <div class="abs hero-photo" role="img" aria-label="Portrait of a woman with glowing skin resting her chin on her hand"></div>
  <div class="abs ring"></div>
  <div class="abs disc">
    <h1>ENHANCE &nbsp;|<br>ENRICH &nbsp;| &nbsp;ENGAGE</h1>
    <p>Welcome to Orvia Skin Clinic, leading supplier of skincare and beauty products.</p>
    <div class="btn-gold">SHOP NOW &#10140;</div>
  </div>
</section>
<div class="abs logo"><span>Orvia</span></div>

<section class="abs welcome">
  <h2 class="display">WELCOME TO ORVIA SKIN CLINIC</h2>
  <p>Welcome to Orvia Skin Clinic, leading supplier of skincare and beauty products. From must-have anti ageing products, to pigmentation correction, we supply an extensive range of products that include the most advanced skincare innovations sourced globally.</p>
  <div class="tab"><span>READ MORE</span></div>
</section>

<section class="abs featured">
  <h2 class="abs section-title display" style="top:78px">FEATURED PRODUCTS</h2>
  <div class="abs fcard" style="left:95px">
    <div class="abs back"></div>
    <div class="abs img"><i role="img" aria-label="Vitamin supplement bottles"></i></div>
    <div class="abs body"><h3>Vitamins</h3><p>Originally created in 2007, improved on in 2012 and upgraded for 2015, Dermalite™ is a combination of powerful yet safe skin whitening and lightening agents.</p><div class="btn-gold">SHOP NOW</div></div>
  </div>
  <div class="abs fcard" style="left:624px">
    <div class="abs back"></div>
    <div class="abs img"><i role="img" aria-label="Nootropic supplement bottles"></i></div>
    <div class="abs body"><h3>Nootropics</h3><p>Originally created in 2007, improved on in 2012 and upgraded for 2015, Dermalite™ is a combination of powerful yet safe skin whitening and lightening agents.</p><div class="btn-gold">SHOP NOW</div></div>
  </div>
</section>
<svg class="abs arrow" style="left:33px" width="30" height="16" viewBox="0 0 30 16"><path d="M28 8H4M10 2L3 8l7 6" fill="none" stroke="#c4a46b" stroke-width="3"/></svg>
<svg class="abs arrow" style="left:1138px" width="30" height="16" viewBox="0 0 30 16"><path d="M2 8h24M20 2l7 6-7 6" fill="none" stroke="#c4a46b" stroke-width="3"/></svg>

<h2 class="abs section-title display" style="left:0;top:1668px">BEST SELLER</h2>
<div class="abs pcard" style="left:111px"><div class="img" role="img" aria-label="Body care bottles"></div><h4>BODY CARE</h4><div class="rate"><span class="stars">★★★★★</span> (1 customer review)</div><div class="price">$40.25</div><div class="cart">ADD TO CART</div></div>
<div class="abs pcard" style="left:360px"><div class="img" role="img" aria-label="Buzz product bottles"></div><h4>BUZZ PRODUCT</h4><div class="rate"><span class="stars">★★★★★</span> (1 customer review)</div><div class="price">$40.25</div><div class="cart">ADD TO CART</div></div>
<div class="abs pcard" style="left:608px"><div class="img" role="img" aria-label="Hair product bottles"></div><h4>HAIR PRODUCT</h4><div class="rate"><span class="stars">★★★★★</span> (1 customer review)</div><div class="price">$40.25</div><div class="cart">ADD TO CART</div></div>
<div class="abs pcard" style="left:856px"><div class="img" role="img" aria-label="Skin product bottles"></div><h4>SKIN PRODUCT</h4><div class="rate"><span class="stars">★★★★★</span> (1 customer review)</div><div class="price">$40.25</div><div class="cart">ADD TO CART</div></div>

<div class="abs promo" style="left:111px">
  <div class="photo" role="img" aria-label="Profiles of three women with clear skin" style="left:0;width:235px;background:linear-gradient(90deg,#8a5a42,#d4a488 60%,#c4a46b)"></div>
  <h5 style="left:262px">Lorem ipsum dolor<br>adipiscing elit</h5>
  <div class="btn-dark" style="left:263px">SHOP NOW &#10140;</div>
</div>
<div class="abs promo" style="left:616px">
  <div class="photo" role="img" aria-label="Smiling woman touching her cheek" style="left:0;width:275px;background:linear-gradient(90deg,#c4a46b,#e8c7b3 45%,#d9b096 80%,#c4a46b)"></div>
  <h5 style="left:279px">Lorem ipsum dolor<br>adipiscing elit</h5>
  <div class="btn-dark" style="left:280px">SHOP NOW &#10140;</div>
</div>

<h2 class="abs section-title display" style="left:0;top:2518px">WHAT OUR CLIENTS SAY</h2>
<div class="abs tcard" style="left:111px"><p>Sed ut perspiciatis unde omnis iste natus error sit voluptatem accusantium doloremque laudantium, totam rem aperiam, eaque ipsa</p></div>
<div class="abs tcard" style="left:445px"><p>Sed ut perspiciatis unde omnis iste natus error sit voluptatem accusantium doloremque laudantium, totam rem aperiam, eaque ipsa</p></div>
<div class="abs tcard" style="left:779px"><p>Sed ut perspiciatis unde omnis iste natus error sit voluptatem accusantium doloremque laudantium, totam rem aperiam, eaque ipsa</p></div>
<div class="abs avatar" role="img" aria-label="Client portrait" style="left:221px"></div>
<div class="abs avatar" role="img" aria-label="Client portrait" style="left:555px"></div>
<div class="abs avatar" role="img" aria-label="Client portrait" style="left:889px"></div>
<div class="abs tname" style="left:111px">Clara Wendt, <small>Chairman Kelto</small><span class="stars">★★★★★</span></div>
<div class="abs tname" style="left:445px">Nadia Orme, <small>Project Manager</small><span class="stars">★★★★★</span></div>
<div class="abs tname" style="left:779px">Tomas Reyland, <small>Chairman Kelto</small><span class="stars">★★★★★</span></div>

<footer class="abs footer">
  <h6 style="left:114px">COMPANY</h6>
  <ul style="left:114px"><li>Home</li><li>About</li><li>Products</li><li>Shop now</li><li>Sign in</li></ul>
  <div class="vline" style="left:289px"></div>
  <h6 style="left:380px">INFORMATION</h6>
  <ul style="left:380px"><li>Terms &amp; Conditions</li><li>Privacy Policy</li><li>Disclaimer</li><li>Site Map</li><li>Categories</li></ul>
  <div class="vline" style="left:581px"></div>
  <h6 style="left:702px">SUBSCRIBE OUR NEWSLETTER</h6>
  <div class="abs note">Subscribe to our mailing list to receives daily updates direct to your inbox!</div>
  <div class="abs email">Email Address</div>
  <div class="abs sub">SUBSCRIBE</div>
  <span class="social" style="left:699px"><i></i></span>
  <span class="social" style="left:742px"><i></i></span>
  <span class="social" style="left:785px"><i></i></span>
  <span class="social" style="left:828px"><i></i></span>
  <div class="abs rule"></div>
  <div class="abs copy">Copyrights © Orvia Health 2021 | Allrights Reserved</div>
</footer>

</div>
</body>
</html>
```